wine label for a new vineyard

We have developing vineyard which is just starting production. It izs called Amber Hollow Vineyard. It's in rural Australia and the vineyard is on top of a hill where a prominent tree type is pine (technically Calitris). We want a wine label that incorporates these elements (pine trees, hill or ridge). The calitris pines are statuesque in shape, with sillouetes varying from Lombardy pines to Pencil pines. People often chose wines by the label and we are aiming for the upper end of the market so want a label which encourages buyers to believe that this is a sophisticated product. We need to be able to superimpose the grape variety, year and other information so it needs to be uncluttered design.

Target Market(s)

Experienced and discriminating wine drinkers. Prepared to pay $ 20 for a wine they appreciate.

Industry/Entity Type

Product

Requirements
Must have
• Some element of pines and ridge (or hill) so that people associate the name and the label design.
A label which leads the viewer to believe that this is a high quality product.
Nice to have
• We would like to be able to use some elements from the label as a logo.
Should not have
• Jokey wine labels are fashionable but we don't think they suit our segement of the market.

```html
<!DOCTYPE html>
<html lang="en">
<head>
<meta charset="utf-8">
<title>Amber Hollow Vineyard – Wine Label</title>
<link rel="stylesheet" href="https://fonts.googleapis.com/css2?family=Cinzel:wght@400;500&family=Crimson+Text:wght@400&display=swap">
<style>
  :root {
    --backdrop: #f3f1f3;
    --frame-dark: #3b3634;
    --frame-edge: #6d5b53;
    --paper-light: #ffffff;
    --paper-shade: #dcdcdd;
    --ink: #141212;
    --ink-soft: #3a3838;
    --wine-red: #8e2a2e;
    --rule: #b9b9b9;
    --fine-print: #b3b3b3;
  }
  * { margin: 0; padding: 0; box-sizing: border-box; }
  html, body {
    width: 1200px; height: 1000px; overflow: hidden;
    background: var(--backdrop);
  }
  .canvas { position: relative; width: 1200px; height: 1000px; }

  .label {
    position: absolute;
    width: 754px; height: 510px;
    transform-origin: top left;
  }
  .label--front { left: 223px; top: 84px; }
  .label--neck  { left: 402px; top: 670px; transform: scale(0.524); }

  .label__frame { position: absolute; inset: 0; width: 100%; height: 100%; }

  .label__emblem {
    position: absolute; left: 282px; top: 50px; width: 215px; height: 150px;
    background: radial-gradient(ellipse at 40% 55%, rgba(40,38,38,0.55) 0%, rgba(90,90,90,0.3) 45%, rgba(200,200,200,0) 72%);
    border-radius: 50%;
  }

  .label__name {
    position: absolute; left: 0; right: 0; top: 218px;
    text-align: center;
    font-family: "Cinzel", serif; font-weight: 400;
    font-size: 64px; line-height: 84px; color: var(--ink);
    letter-spacing: 1px;
  }
  .label__name .initial { font-size: 82px; }

  .label__estate {
    position: absolute; left: 0; right: 0; top: 316px;
    text-align: center;
    font-family: "Cinzel", serif; font-size: 24px; line-height: 30px;
    letter-spacing: 6px; color: var(--ink-soft);
  }

  .label__rule {
    position: absolute; left: 202px; top: 374px; width: 350px; height: 1px;
    background: var(--rule);
  }

  .label__variety {
    position: absolute; left: 0; right: 0; top: 398px;
    text-align: center;
    font-family: "Crimson Text", serif; font-size: 36px; line-height: 46px;
    color: var(--wine-red);
  }

  .label__alcohol {
    position: absolute; left: 27px; top: 318px; height: 130px;
    writing-mode: vertical-rl; transform: rotate(180deg);
    font-family: "Crimson Text", serif; font-size: 13px; letter-spacing: 0.5px;
    color: var(--fine-print); text-align: center;
  }
</style>
</head>
<body>
<main class="canvas">

  <section class="label label--front" aria-label="Front wine label">
    <svg class="label__frame" viewBox="0 0 754 510" aria-hidden="true">
      <defs>
        <radialGradient id="paper-front" cx="50%" cy="45%" r="65%">
          <stop offset="0" stop-color="var(--paper-light)"/>
          <stop offset="1" stop-color="var(--paper-shade)"/>
        </radialGradient>
      </defs>
      <polygon points="38,1 716,1 753,38 753,472 716,509 38,509 1,472 1,38" fill="var(--frame-dark)" stroke="var(--frame-edge)" stroke-width="2"/>
      <polygon points="46,14 708,14 740,46 740,464 708,496 46,496 14,464 14,46" fill="url(#paper-front)" stroke="var(--frame-edge)" stroke-width="1.5"/>
    </svg>
    <div class="label__emblem" role="img" aria-label="Illustration of a bare branching tree fading from black to grey"></div>
    <h1 class="label__name"><span class="initial">A</span>MBER <span class="initial">H</span>OLLOW</h1>
    <p class="label__estate">VINEYARD</p>
    <div class="label__rule"></div>
    <p class="label__variety">Pino Nior</p>
    <p class="label__alcohol">ALC 13% BY VOL</p>
  </section>

  <section class="label label--neck" aria-label="Small wine label">
    <svg class="label__frame" viewBox="0 0 754 510" aria-hidden="true">
      <defs>
        <radialGradient id="paper-neck" cx="50%" cy="45%" r="65%">
          <stop offset="0" stop-color="var(--paper-light)"/>
          <stop offset="1" stop-color="var(--paper-shade)"/>
        </radialGradient>
      </defs>
      <polygon points="38,1 716,1 753,38 753,472 716,509 38,509 1,472 1,38" fill="var(--frame-dark)" stroke="var(--frame-edge)" stroke-width="3"/>
      <polygon points="46,16 708,16 738,46 738,464 708,494 46,494 16,464 16,46" fill="url(#paper-neck)" stroke="var(--frame-edge)" stroke-width="2"/>
    </svg>
    <div class="label__emblem" role="img" aria-label="Illustration of a bare branching tree fading from black to grey"></div>
    <p class="label__name"><span class="initial">A</span>MBER <span class="initial">H</span>OLLOW</p>
    <p class="label__estate">VINEYARD</p>
    <div class="label__rule"></div>
    <p class="label__variety">Pino Nior</p>
    <p class="label__alcohol">ALC 13% BY VOL</p>
  </section>

</main>
</body>
</html>
```